Product Label Design

Need a product design for our Epsom salt product, needs to have a luxurious simple feel to it. The picture attached is our brand and wordage on it, the bag we think should be a stand up bag that should be offwhite/creme color. The other picture are products that we like. We updated the packaging to be a Kraft tube box, please see the attached photo for dimensions.

```html
<!DOCTYPE html>
<html lang="en">
<head>
<meta charset="utf-8">
<title>Halden Brighten – Epsom Salt Pouch Label</title>
<link href="https://fonts.googleapis.com/css2?family=Montserrat:wght@600;700;800&display=swap" rel="stylesheet">
<style>
  :root {
    --backdrop: #b4b4b4;
    --pouch-creme: #efebe6;
    --pouch-edge: #e2ddd6;
    --ink-navy: #1d1a38;
    --band-black: #121212;
    --band-text: #f3f1ee;
  }
  * { box-sizing: border-box; margin: 0; padding: 0; }
  html, body {
    width: 1200px;
    height: 928px;
    overflow: hidden;
    background: var(--backdrop);
    font-family: "Montserrat", sans-serif;
  }
  .canvas {
    width: 1200px;
    height: 928px;
    display: flex;
    align-items: center;
    justify-content: center;
  }
  .pouch-label {
    width: 560px;
    height: 830px;
    background: var(--pouch-creme);
    border: 1px solid var(--pouch-edge);
    border-radius: 14px;
    display: flex;
    flex-direction: column;
    align-items: center;
    color: var(--ink-navy);
    position: relative;
  }
  .seal-line {
    position: absolute;
    top: 64px;
    left: 28px;
    right: 28px;
    height: 3px;
    background: var(--pouch-edge);
    border-radius: 2px;
  }
  .brand-name {
    margin-top: 210px;
    font-size: 66px;
    font-weight: 800;
    letter-spacing: 1px;
    line-height: 1;
  }
  .product-name {
    margin-top: 40px;
    font-size: 44px;
    font-weight: 800;
    line-height: 1;
    letter-spacing: 0.5px;
  }
  .product-desc {
    margin-top: 40px;
    font-size: 20px;
    font-weight: 700;
    line-height: 1.3;
    text-align: center;
    letter-spacing: 0.3px;
  }
  .ingredient-band {
    margin-top: 24px;
    width: 356px;
    height: 30px;
    background: var(--band-black);
    border-radius: 2px;
    display: flex;
    align-items: center;
    justify-content: space-between;
    padding: 0 6px;
    color: var(--band-text);
    font-size: 19px;
    font-weight: 700;
    white-space: nowrap;
  }
  .net-weight {
    margin-top: auto;
    margin-bottom: 92px;
    font-size: 17px;
    font-weight: 700;
    letter-spacing: 0.3px;
  }
</style>
</head>
<body>
  <main class="canvas">
    <section class="pouch-label">
      <div class="seal-line"></div>
      <h1 class="brand-name">Halden</h1>
      <h2 class="product-name">BRIGHTEN</h2>
      <p class="product-desc">US Sourced Pure Epsom Salt<br>(Magnesium Sulfate)</p>
      <div class="ingredient-band">
        <span class="ingredient">+ Abies sibirica</span>
        <span class="ingredient">+ Fir Balsam</span>
      </div>
      <p class="net-weight">NET WT. SLBS (1360g)</p>
    </section>
  </main>
</body>
</html>
```